Quillmere Climate Business Card Design

Design new, 2 sides, business cards for a residential and light commercial heating, air conditioning contractor.

Target Market(s)

Homeowners, small businesses

Industry/Entity Type

Business

Contact Information for Business Card

Dominic Westerhall
Phone - 862-415-2736
Email
Address - PO box 518
Brightwater NJ 07912
Website - www.HarborBreezeLLC.example

Requirements
Must have
• logo, company colors, standard size with no die cut, so I can use nova stamp

```html
<!DOCTYPE html>
<html lang="en">
<head>
<meta charset="utf-8">
<title>Quillmere Climate Business Card</title>
<link rel="stylesheet" href="https://fonts.googleapis.com/css2?family=Arimo:wght@400;700&display=swap">
<style>
  :root {
    --page-bg: #3b3532;
    --card-black: #111213;
    --text-white: #e9e9e9;
    --brand-red: #b8242c;
    --accent-orange: #e48a1c;
    --silver: #b9bcbf;
    --rule: #d8d8d8;
  }
  * { margin: 0; padding: 0; box-sizing: border-box; }
  html, body {
    width: 1200px; height: 864px; overflow: hidden;
    background: var(--page-bg);
    font-family: "Arimo", Arial, sans-serif;
  }
  .canvas { position: relative; width: 1200px; height: 864px; }
  .card {
    position: absolute; left: 260px;
    width: 680px; height: 388px;
    background: var(--card-black);
    box-shadow: 0 10px 28px rgba(0,0,0,0.45);
  }
  .card-back { top: 30px; }
  .card-front { top: 446px; }

  .back-wordmark {
    position: absolute; inset: 0;
    display: flex; align-items: center; justify-content: center;
    font-size: 50px; font-weight: 700;
    color: var(--silver);
  }

  .person { position: absolute; left: 48px; top: 84px; }
  .person-name { font-size: 22px; line-height: 26px; color: var(--brand-red); }
  .person-title { font-size: 16px; line-height: 20px; color: var(--accent-orange); margin-top: 2px; }

  .divider {
    position: absolute; left: 48px; width: 336px; top: 148px;
    height: 1.5px; background: var(--rule);
  }
  .front-wordmark {
    position: absolute; right: 36px; top: 132px;
    width: 250px; text-align: right;
    font-size: 28px; line-height: 34px; font-weight: 700;
    color: var(--brand-red); white-space: nowrap;
  }
  .address-rule {
    position: absolute; right: 36px; width: 250px; top: 250px;
    height: 1.5px; background: var(--rule);
  }

  .contacts {
    position: absolute; left: 48px; top: 166px;
    list-style: none;
    font-size: 14px; color: var(--text-white);
  }
  .contacts li { display: flex; align-items: center; gap: 12px; height: 24px; }
  .contacts svg { width: 14px; height: 14px; fill: var(--brand-red); flex: none; }

  .address {
    position: absolute; right: 36px; top: 270px;
    text-align: right; font-size: 15px; line-height: 26px;
    font-style: normal; color: var(--text-white);
  }
  .address .web { letter-spacing: 1.5px; }
</style>
</head>
<body>
<main class="canvas">
  <section class="card card-back" aria-label="Card back">
    <div class="back-wordmark">Quillmere Climate</div>
  </section>

  <section class="card card-front" aria-label="Card front">
    <div class="person">
      <div class="person-name">Dominic Westerhall</div>
      <div class="person-title">President</div>
    </div>

    <div class="divider"></div>
    <div class="front-wordmark">Quillmere Climate</div>
    <div class="address-rule"></div>

    <ul class="contacts">
      <li>
        <svg viewBox="0 0 16 16" aria-hidden="true"><path d="M1 5c0-2 3-3 7-3s7 1 7 3v2h-4V5.5H5V7H1z"/><rect x="3" y="8" width="10" height="7" rx="1"/></svg>
        <span>862 415 2736</span>
      </li>
      <li>
        <svg viewBox="0 0 16 16" aria-hidden="true"><path d="M4 0h8a1 1 0 0 1 1 1v14a1 1 0 0 1-1 1H4a1 1 0 0 1-1-1V1a1 1 0 0 1 1-1zm1 2v10h6V2z"/></svg>
        <span>862 415 2740</span>
      </li>
      <li>
        <svg viewBox="0 0 16 16" aria-hidden="true"><rect x="4" y="1" width="8" height="5"/><rect x="1" y="6" width="14" height="9" rx="1"/></svg>
        <span>862 415 2751</span>
      </li>
      <li>
        <svg viewBox="0 0 16 16" aria-hidden="true"><path d="M1 3h14v10H1zm1.5 1.2L8 8.5l5.5-4.3z" fill-rule="evenodd"/></svg>
        <span>dominic@quillmereclimate.example</span>
      </li>
    </ul>

    <address class="address">
      <div>PO box 518</div>
      <div>Brightwater NJ 07912</div>
      <div class="web">www.QuillmereClimateLLC.example</div>
    </address>
  </section>
</main>
</body>
</html>
```